Velborix advertisement one page flyer design

We need a flyer design for our company to advertise what we offer, it only needs to be one sided, approx A5 in size.
Our logo: http://velborix-example.com/images/logo.png (I will provide in high-res later)
We offer, website design, development, bespoke applications. We would like to advertise that we can be hired for short term contracts for companies who need help with their work load.
Some of, but not limited to the systems we build are content management systems, e-commerce systems & event booking systems.
Our strap line is "We design, develop and deliver", a nice sleek redesign of the image on our website would be nice, but not required 100% - http://velborix-example.com/
Other details to put on the flyer:-
Email: hello@velborix-example.com
Tel: 01632 960 417
Address: Velborix Ltd, Crest Suites, Dunmoor Road, Cheltenham, GL53 4QT
We welcome any other ideas.

```html
<!DOCTYPE html>
<html lang="en">
<head>
<meta charset="utf-8">
<title>Velborix Flyer</title>
<link rel="stylesheet" href="https://fonts.googleapis.com/css2?family=Mali:wght@500&family=Baloo+2:wght@600;800&family=Fjalla+One&family=Arimo:wght@400;700&display=swap">
<style>
  :root {
    --backdrop: #3b2419;
    --orange: #f2640f;
    --orange-deep: #c8390a;
    --red-dark: #8e1c06;
    --glow: #ffb347;
    --panel-grey: #d3d3d3;
    --ink: #111111;
    --logo-grey: #555555;
    --white: #ffffff;
  }
  * { margin: 0; padding: 0; box-sizing: border-box; }
  html, body { width: 891px; height: 1200px; overflow: hidden; }
  body { background: var(--backdrop); position: relative; }

  .flyer {
    position: absolute; left: 57px; top: 47px;
    width: 778px; height: 1105px;
    background: var(--panel-grey);
    overflow: hidden;
  }

  .hero-photo {
    position: absolute; left: 0; top: 0; width: 778px; height: 565px;
    background:
      radial-gradient(ellipse 340px 300px at 590px 230px, var(--glow) 0%, rgba(255,150,40,0.55) 40%, transparent 75%),
      linear-gradient(135deg, var(--orange) 0%, var(--orange-deep) 45%, var(--red-dark) 75%, var(--orange-deep) 100%);
  }

  .intro {
    position: absolute; left: 40px; width: 560px;
    font-family: "Mali", cursive;
    font-weight: 500; font-size: 26px; line-height: 43px;
    color: var(--white);
  }
  .intro--offer { top: 24px; }
  .intro--contract { top: 138px; }

  .how-it-works {
    position: absolute; left: 40px; top: 338px;
    font-family: "Mali", cursive; font-weight: 500;
    font-size: 46px; color: var(--white);
  }

  .strapline-word {
    position: absolute;
    font-family: "Baloo 2", sans-serif; font-weight: 800;
    color: var(--white);
    -webkit-text-stroke: 3px var(--orange);
    paint-order: stroke fill;
    text-shadow: 0 0 0 var(--orange), 4px 4px 0 var(--orange), -4px -4px 0 var(--orange), 4px -4px 0 var(--orange), -4px 4px 0 var(--orange);
    transform: rotate(-9deg);
    transform-origin: left center;
    line-height: 1;
    white-space: nowrap;
  }
  .strapline-word small { font-size: 48px; }
  .strapline-word--design { left: 120px; top: 440px; font-size: 86px; }
  .strapline-word--develop { left: 295px; top: 545px; font-size: 84px; }
  .strapline-word--deliver { left: 430px; top: 610px; font-size: 90px; }

  .solutions-title {
    position: absolute; left: 38px; top: 635px;
    font-family: "Mali", cursive; font-weight: 500;
    font-size: 40px; line-height: 50px; color: var(--ink);
  }

  .service {
    position: absolute; display: flex; align-items: center; gap: 13px;
    font-family: "Fjalla One", sans-serif; font-size: 24px; color: var(--ink);
  }
  .service-icon {
    width: 66px; height: 66px; flex: none;
    background: var(--orange);
    border-radius: 50% 50% 50% 8px;
    display: flex; align-items: center; justify-content: center;
  }
  .service-icon svg { width: 36px; height: 36px; }

  .footer-shapes { position: absolute; left: 0; top: 0; }

  .logo {
    position: absolute; left: 40px; top: 1022px;
    display: flex; align-items: center; gap: 10px;
    font-family: "Baloo 2", sans-serif; font-weight: 600;
    font-size: 60px; line-height: 1; color: var(--logo-grey);
  }
  .logo-dot { width: 30px; height: 30px; border-radius: 50%; background: var(--orange); }

  .contact {
    position: absolute; right: 18px; text-align: right;
    font-family: "Arimo", sans-serif; font-size: 14px; color: var(--ink);
    display: flex; align-items: center; justify-content: flex-end; gap: 8px;
  }
  .contact strong { font-weight: 700; }
  .contact svg { width: 14px; height: 14px; flex: none; }
</style>
</head>
<body>
<main class="flyer">
  <div class="hero-photo" role="img" aria-label="Photo of a hand touching glowing web icons on an orange background"></div>

  <p class="intro intro--offer">We offer website design,<br>development, bespoke application</p>
  <p class="intro intro--contract">We can be hired for short term contract<br>for. companies who need help with<br>then work load</p>

  <h2 class="how-it-works">How It Works?</h2>

  <div class="strapline-word strapline-word--design"><small>We</small> design</div>
  <div class="strapline-word strapline-word--develop">devlop</div>
  <div class="strapline-word strapline-word--deliver">deliver</div>

  <h2 class="solutions-title">Solutions<br>We Provide</h2>

  <div class="service" style="left:36px; top:760px;">
    <span class="service-icon"><svg viewBox="0 0 36 36" fill="none" stroke="#fff" stroke-width="2.5"><rect x="8" y="5" width="20" height="26" rx="2"/><line x1="12" y1="12" x2="24" y2="12"/><line x1="12" y1="18" x2="24" y2="18"/><line x1="12" y1="24" x2="20" y2="24"/></svg></span>
    Content Management
  </div>
  <div class="service" style="left:36px; top:835px;">
    <span class="service-icon"><svg viewBox="0 0 36 36" fill="none" stroke="#fff" stroke-width="2.5"><circle cx="18" cy="18" r="12"/><ellipse cx="18" cy="18" rx="5" ry="12"/><line x1="6" y1="18" x2="30" y2="18"/></svg></span>
    Web Design
  </div>
  <div class="service" style="left:36px; top:908px;">
    <span class="service-icon"><svg viewBox="0 0 36 36" fill="none" stroke="#fff" stroke-width="2.5"><path d="M28 18a10 10 0 1 1-4-8"/><polyline points="25,5 25,11 19,11"/></svg></span>
    Bespoke System
  </div>
  <div class="service" style="left:433px; top:760px;">
    <span class="service-icon"><svg viewBox="0 0 36 36" fill="none" stroke="#fff" stroke-width="2.5"><circle cx="16" cy="17" r="11"/><ellipse cx="16" cy="17" rx="4.5" ry="11"/><line x1="5" y1="17" x2="27" y2="17"/></svg></span>
    e-commerce
  </div>
  <div class="service" style="left:433px; top:833px;">
    <span class="service-icon"><svg viewBox="0 0 36 36" fill="none" stroke="#fff" stroke-width="2.5"><rect x="7" y="11" width="18" height="19" rx="2"/><line x1="14" y1="22" x2="29" y2="6"/></svg></span>
    Subscription System
  </div>
  <div class="service" style="left:433px; top:908px;">
    <span class="service-icon"><svg viewBox="0 0 36 36" fill="none" stroke="#fff" stroke-width="2.5"><rect x="7" y="14" width="22" height="6" rx="2"/><rect x="7" y="23" width="22" height="6" rx="2"/><polyline points="10,6 14,10 18,6"/><polyline points="18,6 22,10 26,6"/></svg></span>
    Domain &amp; Hosting
  </div>

  <svg class="footer-shapes" width="778" height="1105" viewBox="0 0 778 1105" aria-hidden="true">
    <polygon points="0,975 778,1090 778,1105 0,1105" fill="#eeeeee"/>
    <polygon points="0,975 300,1035 300,1105 0,1105" fill="#eeeeee"/>
    <polygon points="288,1035 778,973 778,1105 420,1105" fill="var(--orange)"/>
  </svg>

  <div class="logo"><span class="logo-dot"></span>Velborix</div>

  <p class="contact" style="top:1003px;">Velborix Ltd, Crest Suites,
    <svg viewBox="0 0 14 14"><path d="M7 1a4 4 0 0 1 4 4c0 3-4 8-4 8S3 8 3 5a4 4 0 0 1 4-4z" fill="#111"/><circle cx="7" cy="5" r="1.5" fill="#f2640f"/></svg></p>
  <p class="contact" style="top:1030px; right:40px;">Dunmoor Road, Cheltenham, GL53 4QT</p>
  <p class="contact" style="top:1059px;">Call Us Today <strong>01632 960 417</strong>
    <svg viewBox="0 0 14 14"><path d="M3 1l2 0 1 3-1.5 1a7 7 0 0 0 4 4L10 8l3 1v2a2 2 0 0 1-2 2C6 13 1 8 1 3a2 2 0 0 1 2-2z" fill="#111"/></svg></p>
  <p class="contact" style="top:1083px;">hello@velborix-example.com
    <svg viewBox="0 0 14 14"><rect x="1" y="3" width="12" height="8" fill="#111"/><polyline points="1,3 7,8 13,3" fill="none" stroke="#f2640f" stroke-width="1"/></svg></p>
</main>
</body>
</html>
```